Chiropractic Business Card

I need a business card designed to help me stand apart from my competition. I really like simple, clean designs that appear open and inviting. I would like the designs to incorporate the color blue, green, or both. I really like the attached picture because it highlights that I just don't treat "back pain" and it being a nice computer graphic helps show that I have a modern practice. "Modern practice" meaning merging technology and most current research in my patient care.

My information is:

Lyle Farwick, DC
Phone- (707) 555-0182
Email- drlylefarwick@mailnest.example
Website- www.brevincourtchiropractic.example
Address- 248 Tolliver Street, Sonoma, CA 95999

Jpeg and pdf attached of Brevincourt Chiropractic logo.
Updates

Atmosphere to be clean lines and solid colors to be have gradient fading, but don't want too much going on with the fading. Simple.

Target Market(s)

Active adults who are health conscious between the ages of 20-70

Industry/Entity Type

Computer

Colors
0455a3
85cae6

Requirements
Must have
• Change color of Brevincourt chiropractic logo (maroon) to fit the rest of the design.
Nice to have
• Can separate the running image from the black background to have it work with the design.

```html
<!DOCTYPE html>
<html lang="en">
<head>
<meta charset="utf-8">
<title>Brevincourt Chiropractic – Business Card</title>
<link href="https://fonts.googleapis.com/css2?family=Open+Sans:wght@400;600;700&display=swap" rel="stylesheet">
<style>
  :root {
    --stage: #cfcfcf;
    --card: #050505;
    --violet: #3b3ba6;
    --sky: #1e9fe3;
    --white: #ffffff;
    --muted: #d9d9d9;
  }
  * { box-sizing: border-box; margin: 0; padding: 0; }
  html, body { width: 1200px; height: 894px; overflow: hidden; }
  body {
    background: var(--stage);
    font-family: "Open Sans", Arial, sans-serif;
    position: relative;
  }
  .card {
    position: absolute;
    width: 620px;
    height: 354px;
    background: var(--card);
    overflow: hidden;
    box-shadow: 0 6px 18px rgba(0,0,0,.25);
  }
  .card--front { left: 290px; top: 470px; }
  .card--back  { left: 290px; top: 70px; }
  .card__edge { position: absolute; left: 0; top: 0; width: 620px; height: 60px; }

  .brand {
    position: absolute;
    color: var(--violet);
    font-weight: 700;
    font-size: 27px;
    line-height: 1.05;
    letter-spacing: 1px;
    text-transform: uppercase;
  }
  .card--front .brand { left: 70px; top: 38px; }
  .card--back .brand { left: 200px; top: 60px; }

  .name-marker {
    position: absolute; left: 0; top: 130px;
    width: 30px; height: 56px; background: var(--violet);
  }
  .holder { position: absolute; left: 50px; top: 130px; }
  .holder__name {
    color: var(--white); font-weight: 700; font-size: 30px;
    letter-spacing: 1px; line-height: 1.1; text-transform: uppercase;
  }
  .holder__role {
    color: var(--sky); font-size: 14px; letter-spacing: 5px;
    text-transform: uppercase; margin-top: 2px;
  }

  .contact {
    position: absolute; left: 330px; top: 222px;
    list-style: none; color: var(--white);
    font-size: 13px; font-weight: 600;
  }
  .contact li { display: flex; align-items: flex-start; margin-bottom: 8px; }
  .contact svg { width: 16px; height: 16px; margin-right: 12px; flex: none; fill: var(--sky); }
  .contact span { line-height: 1.25; }

  .social {
    position: absolute; left: 100px; top: 220px; width: 460px;
    display: flex; justify-content: space-between;
    list-style: none; color: var(--muted); font-size: 14px;
  }
  .social li { display: flex; align-items: center; }
  .social__mark { width: 18px; height: 18px; background: var(--sky); margin-right: 10px; }

  .back-tab {
    position: absolute; right: 0; top: 232px;
    width: 14px; height: 42px; background: var(--sky);
  }
</style>
</head>
<body>

  <section class="card card--back" aria-label="Business card back">
    <svg class="card__edge" viewBox="0 0 620 60" aria-hidden="true">
      <path d="M0 0 H620 V28 C470 2 300 8 0 2 Z" fill="var(--sky)"/>
      <path d="M0 0 H620 V20 C470 -2 300 4 0 0 Z" fill="var(--card)"/>
    </svg>
    <div class="brand">Brevincourt<br>Chiropractic</div>
    <ul class="social">
      <li><span class="social__mark"></span>yourname</li>
      <li><span class="social__mark"></span>@yourname</li>
      <li><span class="social__mark"></span>yourname</li>
    </ul>
    <div class="back-tab"></div>
  </section>

  <section class="card card--front" aria-label="Business card front">
    <svg class="card__edge" viewBox="0 0 620 60" aria-hidden="true">
      <path d="M0 0 H620 V22 C430 6 220 4 0 3 Z" fill="var(--violet)"/>
    </svg>
    <div class="brand">Brevincourt<br>Chiropractic</div>

    <div class="name-marker"></div>
    <div class="holder">
      <h1 class="holder__name">Lyle Farwick, DC</h1>
      <p class="holder__role">Chiropractor</p>
    </div>

    <ul class="contact">
      <li>
        <svg viewBox="0 0 16 16"><path d="M8 1 L15 8 H13 V15 H9.5 V10.5 H6.5 V15 H3 V8 H1 Z"/></svg>
        <span>248 Tolliver Street<br>Sonoma, CA 95999</span>
      </li>
      <li>
        <svg viewBox="0 0 16 16"><path d="M8 1a7 7 0 1 0 0 14A7 7 0 0 0 8 1zm0 1.5c.7 0 1.6 1.6 1.9 4.5H6.1C6.4 4.1 7.3 2.5 8 2.5zM2.6 7h2c.1-1.6.4-3 .9-3.9A5.5 5.5 0 0 0 2.6 7zm8.8 0h2a5.5 5.5 0 0 0-2.9-3.9c.5.9.8 2.3.9 3.9zM2.6 9a5.5 5.5 0 0 0 2.9 3.9c-.5-.9-.8-2.3-.9-3.9zm3.5 0c.3 2.9 1.2 4.5 1.9 4.5s1.6-1.6 1.9-4.5zm5.3 0c-.1 1.6-.4 3-.9 3.9A5.5 5.5 0 0 0 13.4 9z"/></svg>
        <span>www.brevincourtchiropractic.example</span>
      </li>
      <li>
        <svg viewBox="0 0 16 16"><path d="M1 3.5h14v9H1z M1.5 4 8 9l6.5-5" fill="none" stroke="var(--sky)" stroke-width="1.4"/></svg>
        <span>drlylefarwick@mailnest.example</span>
      </li>
      <li>
        <svg viewBox="0 0 16 16"><path d="M4 1.5 6.2 4.6 4.9 6.2c.8 1.9 2.3 3.4 4.2 4.2l1.6-1.3 3.1 2.2-1.2 2.6C7.6 14 2 8.4 1.4 3.4z"/></svg>
        <span>(707) 555-0182</span>
      </li>
    </ul>
  </section>

</body>
</html>
```